Brightarc Orthodontics appointment card design

I need appointment cards/ business cards made. Front will be Logo, name, title, email, phone number and location (5263 Walnut Hollow Pkwy, Ste 412, Concord, NC 28027) . the back should have an appointment card (name, time, date) and also 3 addresses listed with a check box so we can check to which location they are going.
Dale Fenwick Orthodontics
- 6735 Orchard Street, Ste 514, Harrisburg, NC 28075
- 3647 Ridgeway Drive NE, Ste 810, Concord, NC 28025
- 2917 Thornbury Corporate Drive, Ste 605, Charlotte, NC 28277
Business card can be horizontal or vertical in Design.
I need to be able to edit it to update and add new employees

Requirements
Must have
• Front:
• - Logo
• - Name & Title (able to be edited)
• - phone (704-555-0186) & Email (need to be able to edit)
• - Address: 5263 Walnut Hollow Pkwy, Ste 412
• Concord, NC 28027
• Back:
• Appointment Card design:
• - Name, time, Date
• - 3 locations w/ a check box so the patient knows where to go:
• Dale Fenwick Orthodontics
• - 6735 Orchard Street, Ste 514, Harrisburg, NC 28075
• - 3647 Ridgeway Drive NE, Ste 810, Concord, NC 28025
• - 2917 Thornbury Corporate Drive, Ste 605, Charlotte, NC 28277

```html
<!DOCTYPE html>
<html lang="en">
<head>
<meta charset="utf-8">
<title>Brightarc Orthodontics – Appointment &amp; Business Card</title>
<link href="https://fonts.googleapis.com/css2?family=Roboto:wght@400;500;700;900&display=swap" rel="stylesheet">
<style>
  :root {
    --brand-blue: #1479bd;
    --brand-blue-dark: #0f67a8;
    --ink: #3a3a3a;
    --line: #555;
    --card: #ffffff;
    --backdrop: #3b3b3d;
  }
  * { box-sizing: border-box; margin: 0; padding: 0; }
  html, body { width: 1200px; height: 1000px; overflow: hidden; }
  body {
    background: var(--backdrop);
    font-family: "Roboto", Arial, sans-serif;
    color: var(--ink);
    position: relative;
  }
  .card {
    position: absolute;
    left: 250px;
    width: 700px;
    height: 400px;
    background: var(--card);
    border-radius: 26px;
    overflow: hidden;
    box-shadow: 0 14px 30px rgba(0,0,0,.45);
  }
  .card--back { top: 70px; }
  .card--front { top: 530px; }

  .brand {
    display: flex; align-items: center; justify-content: center; gap: 10px;
    color: var(--brand-blue);
    font-weight: 700;
    white-space: nowrap;
  }
  .brand__dot { border-radius: 50%; background: var(--brand-blue); flex: none; }

  /* Back: appointment side */
  .card--back .brand { margin-top: 26px; font-size: 30px; }
  .card--back .brand__dot { width: 16px; height: 16px; }
  .appointment-title {
    text-align: center; color: var(--brand-blue);
    font-weight: 700; font-size: 22px; margin-top: 8px;
  }
  .field {
    position: absolute; display: flex; align-items: flex-end; gap: 8px;
    font-size: 14px; color: var(--ink);
  }
  .field__rule { flex: 1; border-bottom: 1px solid var(--line); height: 1px; margin-bottom: 3px; }
  .field--name { left: 40px; right: 40px; top: 128px; }
  .field--date { left: 40px; right: 40px; top: 168px; }
  .field--time { left: 360px; right: 40px; top: 208px; }
  .ampm { position: absolute; top: 240px; right: 40px; display: flex; gap: 18px; font-size: 14px; }
  .check { display: inline-block; width: 14px; height: 14px; border: 1.5px solid var(--brand-blue-dark); vertical-align: -2px; margin-right: 5px; }
  .practice {
    position: absolute; top: 262px; left: 0; right: 0; text-align: center;
    font-size: 15px; color: var(--ink);
  }
  .practice strong { color: var(--brand-blue); font-size: 20px; font-weight: 700; margin-right: 4px; }
  .locations {
    position: absolute; top: 298px; left: 30px; right: 30px;
    display: flex; justify-content: space-between; list-style: none;
  }
  .location { width: 200px; font-size: 13px; line-height: 1.3; text-align: center; }
  .location .check { display: block; margin: 0 auto 6px; }
  .card--back .band { position: absolute; left: 0; right: 0; bottom: 0; height: 14px; background: var(--brand-blue); }

  /* Front: business card side */
  .card--front .brand { margin-top: 74px; font-size: 50px; }
  .card--front .brand__dot { width: 26px; height: 26px; }
  .person { position: absolute; top: 176px; left: 0; right: 0; text-align: center; }
  .person__name { color: var(--brand-blue); font-weight: 700; font-size: 28px; letter-spacing: .5px; }
  .person__title { font-size: 18px; color: var(--ink); margin-top: 2px; }
  .card--front .band {
    position: absolute; left: 0; right: 0; bottom: 0; height: 140px;
    background: var(--brand-blue);
    display: flex; align-items: center; justify-content: center; gap: 26px;
    color: #fff;
  }
  .address { text-align: right; font-size: 19px; line-height: 1.3; }
  .divider { width: 2px; height: 70px; background: #fff; }
  .contact { list-style: none; font-size: 19px; line-height: 1.5; }
  .contact li { display: flex; align-items: center; gap: 8px; }
  .contact svg { width: 16px; height: 16px; flex: none; }
</style>
</head>
<body>

<section class="card card--back" aria-label="Appointment card">
  <div class="brand"><span class="brand__dot"></span>Brightarc Orthodontics</div>
  <h2 class="appointment-title">Next Appointment</h2>

  <div class="field field--name"><span>Name</span><span class="field__rule"></span></div>
  <div class="field field--date"><span>Date</span><span class="field__rule"></span></div>
  <div class="field field--time"><span>Time</span><span class="field__rule"></span></div>
  <div class="ampm"><span><span class="check"></span>AM</span><span><span class="check"></span>PM</span></div>

  <p class="practice"><strong>Dale Fenwick</strong>Orthodontics</p>

  <ul class="locations">
    <li class="location"><span class="check"></span>6735 Orchard Street, Ste 514,<br>Harrisburg, NC 28075</li>
    <li class="location"><span class="check"></span>3647 Ridgeway Drive NE, Ste 810,<br>Concord, NC 28025</li>
    <li class="location"><span class="check"></span>2917 Thornbury Corporate Drive,<br>Ste 605, Charlotte, NC 28277</li>
  </ul>
  <div class="band"></div>
</section>

<section class="card card--front" aria-label="Business card">
  <div class="brand"><span class="brand__dot"></span>Brightarc Orthodontics</div>

  <div class="person">
    <p class="person__name">DALE FENWICK</p>
    <p class="person__title">Orthodontics</p>
  </div>

  <div class="band">
    <p class="address">5263 Walnut Hollow Pkwy,<br>Ste 412 - Concord, NC 28027</p>
    <span class="divider"></span>
    <ul class="contact">
      <li>
        <svg viewBox="0 0 16 16" aria-hidden="true"><path fill="#fff" d="M3.6 1.5l2.3 2.6-1.3 1.8c.9 2 2.5 3.6 4.5 4.5l1.8-1.3 2.6 2.3-1.5 2.2C7 13.2 2.8 9 1.4 3z"/></svg>
        704-555-0186
      </li>
      <li>
        <svg viewBox="0 0 16 16" aria-hidden="true"><rect x="1" y="3" width="14" height="10" rx="1" fill="#fff"/><path d="M1.5 3.8L8 9l6.5-5.2" fill="none" stroke="#1479bd" stroke-width="1.4"/></svg>
        dfenwick@brightarc-ortho.com
      </li>
    </ul>
  </div>
</section>

</body>
</html>
```